Automotive component supplier needs a business card design

We need a business card design for our company called Velran Global Components Ltd based in the UK. We are a supplier of interior and exterior components to premium car manufacturers such as Corvel Ashby, Hadley Fenn, Marquist and Tavarelli. We would like to see a modern business card design that uses the colour blue.

Target Market(s)

Premium automotive car manufacturers.

Industry/Entity Type

Automotive

Contact Information for Business Card

Company Name : Velran Global Components Limited
Address: 17 Marlow Yard, Upper Heath, Warwick, CV31 8QL, United Kingdom
Web Address : www.velrancomponents-example.co.uk

Font styles to use
Other font styles liked:
• Helvetica

Colors
3176b5
0255a3
85acd3
cfdeed
cee9f5
85cae6
34a6d7
0692cd
9bcb3c

Requirements
Must have
• Clear company logo and a mixture of blue colours.
Nice to have
• A high quality modern image.
Should not have
• Multiple colours.

```html
<!DOCTYPE html>
<html lang="en">
<head>
<meta charset="utf-8">
<title>Velran Global Components – Business Card</title>
<link rel="stylesheet" href="https://fonts.googleapis.com/css2?family=Arimo:wght@400;700&display=swap">
<style>
  :root {
    --stage: #2b2b2d;
    --card-black: #050505;
    --blue-deep: #0692cd;
    --blue-main: #34a6d7;
    --blue-pattern: #1f95cf;
    --green: #9bcb3c;
    --white: #ffffff;
  }
  * { box-sizing: border-box; margin: 0; padding: 0; }
  html, body { width: 1200px; height: 900px; overflow: hidden; }
  body {
    background: var(--stage);
    font-family: "Arimo", Helvetica, Arial, sans-serif;
    position: relative;
  }
  .card {
    position: absolute;
    width: 600px;
    height: 343px;
    overflow: hidden;
    box-shadow: 0 10px 30px rgba(0,0,0,.45);
  }

  /* Front face */
  .card--front { left: 80px; top: 110px; background: var(--blue-main); }
  .card__pattern {
    position: absolute; inset: 0;
    background: linear-gradient(135deg, var(--blue-main), var(--blue-pattern));
  }
  .brand {
    position: absolute;
    display: flex; align-items: center; gap: 10px;
    color: var(--white);
    font-weight: 700;
    letter-spacing: .06em;
    text-transform: uppercase;
    line-height: 1.1;
  }
  .brand__dot {
    width: 12px; height: 12px; border-radius: 50%;
    background: var(--green); flex: none;
  }
  .card--front .brand { right: 40px; bottom: 60px; font-size: 22px; }

  /* Back face */
  .card--back { left: 520px; top: 450px; background: var(--card-black); }
  .card--back .brand {
    left: 40px; bottom: 92px;
    width: 200px;
    font-size: 20px;
    color: var(--blue-deep);
  }
  .brand__name { display: block; }
  .info-disc {
    position: absolute;
    left: 255px; top: -95px;
    width: 520px; height: 520px;
    border-radius: 50%;
    border: 7px solid var(--green);
    background: linear-gradient(160deg, var(--blue-main) 0%, var(--blue-deep) 100%);
  }
  .contact {
    position: absolute;
    right: 26px; top: 40px;
    width: 300px;
    text-align: right;
    color: var(--white);
  }
  .contact__name { font-size: 20px; font-weight: 700; letter-spacing: .1em; text-transform: uppercase; }
  .contact__role { font-size: 13px; color: var(--green); margin-top: 3px; }
  .contact__list { list-style: none; margin-top: 18px; font-size: 12.5px; line-height: 1.45; }
  .contact__list li { display: flex; justify-content: flex-end; align-items: center; gap: 8px; }
  .contact__icon { width: 11px; height: 11px; flex: none; }
  .contact__spacer { width: 11px; flex: none; }
  .contact__list .gap { margin-top: 10px; }
</style>
</head>
<body>

  <section class="card card--front" aria-label="Card front">
    <div class="card__pattern" role="img" aria-label="Faint repeating brand pattern across blue background"></div>
    <div class="brand"><span class="brand__dot"></span>Velran Global Components</div>
  </section>

  <section class="card card--back" aria-label="Card back">
    <div class="info-disc"></div>
    <div class="brand"><span class="brand__dot"></span><span class="brand__name">Velran Global<br>Components</span></div>

    <div class="contact">
      <p class="contact__name">Dorian Pell</p>
      <p class="contact__role">Director</p>
      <ul class="contact__list">
        <li>17 Marlow Yard, Upper Heath<span class="contact__spacer"></span></li>
        <li>Warwick, CV31 8QL, UK<span class="contact__spacer"></span></li>
        <li class="gap">780 555-0142
          <svg class="contact__icon" viewBox="0 0 12 12" aria-hidden="true"><path d="M3 1l2 2.5-1.2 1.3a7 7 0 0 0 3.4 3.4L8.5 7 11 9l-1.3 2C5 11 1 7 1 2.3z" fill="#9bcb3c"/></svg>
        </li>
        <li>780 555-0187
          <svg class="contact__icon" viewBox="0 0 12 12" aria-hidden="true"><rect x="3" y="0.5" width="6" height="11" rx="1.2" fill="none" stroke="#9bcb3c" stroke-width="1.3"/><circle cx="6" cy="9.5" r=".8" fill="#9bcb3c"/></svg>
        </li>
        <li class="gap">hello@velrancomponents-example.co.uk
          <svg class="contact__icon" viewBox="0 0 12 12" aria-hidden="true"><rect x="0.5" y="2.5" width="11" height="7" rx="1" fill="#9bcb3c"/><path d="M1 3l5 3.5L11 3" fill="none" stroke="#0692cd" stroke-width="1"/></svg>
        </li>
        <li>www.velrancomponents-example.co.uk
          <svg class="contact__icon" viewBox="0 0 12 12" aria-hidden="true"><circle cx="6" cy="6" r="5" fill="#9bcb3c"/></svg>
        </li>
      </ul>
    </div>
  </section>

</body>
</html>
```